Amber Fox Quest "Your path, my quest"

Individual coaching: life coach & projec Amberfox (amber fox) represents the flight, freedom to be happy. The mission: to be well in his mission in life. sober and soft design which refers professionalism, safety, wellness, balance, personal development. my coordinates = Marta Kovin Life & Project 0462 coach / 31.78.25 marta@amberfoxquest.be

Reason: Business card that refers to the professional (life coaching) and sweetness / freedom of achievement.

Target Market(s)

adults in search of well being, balance for themselves and / or their children

Contact Information for Business Card

Marta Kovin
Life & project coach
0462/31.78.25
marta@amberfoxquest.be

Requirements
Must have
• AMBER FOX QUEST logo tag "Your flight, my mission"
Nice to have
• originality pure appearance, gentle and professional
Should not have
• overdoing banking organization

```html
<!DOCTYPE html>
<html lang="fr">
<head>
<meta charset="utf-8">
<title>Amberfox Quest – cartes de visite</title>
<link href="https://fonts.googleapis.com/css2?family=Ubuntu:ital,wght@0,400;0,500;0,700;1,400&family=Open+Sans:wght@400;600&display=swap" rel="stylesheet">
<style>
  :root {
    --bg: #2b2d31;
    --navy: #1f3f7a;
    --sky: #1d9bd7;
    --grey: #4a4d55;
    --paper: #ffffff;
    --rule: #6b6e75;
    --sky-top: #0f3fa6;
    --sky-mid: #1f63cf;
    --sky-low: #8cc3ee;
  }
  * { margin: 0; padding: 0; box-sizing: border-box; }
  html, body { width: 1200px; height: 960px; overflow: hidden; }
  body { background: var(--bg); position: relative; font-family: "Open Sans", sans-serif; }

  .card {
    position: absolute;
    width: 560px; height: 320px;
    border-radius: 4px;
    overflow: hidden;
    box-shadow: 0 12px 30px rgba(0,0,0,.45);
  }
  .card--front { left: 90px; top: 110px; }
  .card--back { left: 550px; top: 520px; background: var(--paper); }

  .sky {
    position: absolute; inset: 0;
    background:
      radial-gradient(ellipse at 15% 95%, var(--sky-low) 0%, rgba(140,195,238,0) 55%),
      linear-gradient(160deg, var(--sky-mid) 0%, var(--sky-top) 70%, #0b3190 100%);
  }
  .logo {
    font-family: "Ubuntu", sans-serif;
    font-weight: 700;
    color: var(--navy);
    line-height: 1;
    letter-spacing: .5px;
  }
  .tagline {
    font-family: "Ubuntu", sans-serif;
    font-style: italic;
    color: var(--navy);
  }
  .card--front .brand { position: absolute; left: 40px; bottom: 42px; }
  .card--front .logo { font-size: 40px; }
  .card--front .tagline { font-size: 19px; margin-top: 10px; }

  .card--back .brand { position: absolute; left: 40px; top: 128px; width: 250px; }
  .card--back .logo { font-size: 38px; }
  .card--back .tagline { font-size: 19px; margin-top: 12px; }

  .divider {
    position: absolute; left: 310px; top: 28px; bottom: 28px;
    width: 1.5px; background: var(--rule);
  }
  .person { position: absolute; left: 335px; top: 40px; }
  .person__name { font-family: "Ubuntu", sans-serif; font-weight: 700; font-size: 26px; color: var(--navy); }
  .person__role { font-family: "Ubuntu", sans-serif; font-weight: 500; font-size: 15px; color: var(--sky); margin-top: 2px; }

  .contacts { position: absolute; left: 335px; top: 200px; list-style: none; }
  .contacts li {
    display: flex; align-items: center; gap: 12px;
    font-size: 15px; color: var(--grey); height: 26px;
  }
  .contacts svg { width: 18px; height: 18px; flex: none; }
</style>
</head>
<body>

  <section class="card card--front" aria-label="Recto">
    <div class="sky" role="img" aria-label="Ciel bleu avec nuages clairs et vol d'oiseaux blancs"></div>
    <div class="brand">
      <div class="logo">Amberfox Quest</div>
      <div class="tagline">Votre chemin, ma quête</div>
    </div>
  </section>

  <section class="card card--back" aria-label="Verso">
    <div class="brand">
      <div class="logo">Amberfox Quest</div>
      <div class="tagline">Votre chemin, ma quête</div>
    </div>
    <div class="divider"></div>
    <div class="person">
      <div class="person__name">Marta Kovin</div>
      <div class="person__role">Life &amp; project coach</div>
    </div>
    <ul class="contacts">
      <li>
        <svg viewBox="0 0 18 18" aria-hidden="true"><rect width="18" height="18" rx="2" fill="#1f3f7a"/><path d="M6 4.5l2 2-1 1.2c.6 1.3 1.7 2.4 3 3l1.2-1 2 2-1.2 1.5c-3.4-.4-6.7-3.7-7-7z" fill="#fff"/></svg>
        + 32 462 31 78 25
      </li>
      <li>
        <svg viewBox="0 0 18 18" aria-hidden="true"><rect width="18" height="18" rx="2" fill="#1f3f7a"/><rect x="3.5" y="5.5" width="11" height="7" fill="none" stroke="#fff" stroke-width="1.2"/><path d="M3.5 5.5l5.5 4 5.5-4" fill="none" stroke="#fff" stroke-width="1.2"/></svg>
        marta@amberfoxquest.be
      </li>
      <li>
        <svg viewBox="0 0 18 18" aria-hidden="true"><rect width="18" height="18" rx="2" fill="#1f3f7a"/><circle cx="9" cy="9" r="5" fill="none" stroke="#fff" stroke-width="1.2"/><path d="M4 9h10M9 4c-2 2.8-2 7.2 0 10M9 4c2 2.8 2 7.2 0 10" fill="none" stroke="#fff" stroke-width="1"/></svg>
        www.amberfoxquest.be
      </li>
    </ul>
  </section>

</body>
</html>
```